MS word document templates for consultancy

I need the following templates for my business using my logo as branding.

- General report template
- Letter head template
- Tender proposal template

The templates should be sleek and with minimal colors, but with a small amount of green and grey where appropriate (as per attached logo and email signature). Font should be consistent with the text in the email signature.

```html
<!DOCTYPE html>
<html lang="en">
<head>
<meta charset="utf-8">
<title>Northway Partners — Letterhead</title>
<link href="https://fonts.googleapis.com/css2?family=Poppins:wght@300;400;600;700&display=swap" rel="stylesheet">
<style>
  :root {
    --ink: #111111;
    --green: #27954a;
    --grey: #d9d9d9;
    --paper: #ffffff;
  }
  * { margin: 0; padding: 0; box-sizing: border-box; }
  html, body { width: 848px; height: 1200px; overflow: hidden; background: var(--paper); }
  .letterhead {
    position: relative;
    width: 848px;
    height: 1200px;
    font-family: 'Poppins', sans-serif;
    color: var(--ink);
    background: var(--paper);
  }
  .corner { position: absolute; display: block; }
  .corner--top { top: 0; left: 0; }
  .corner--bottom { bottom: 0; left: 0; }

  .brand-name {
    position: absolute;
    left: 84px;
    top: 108px;
    font-size: 37px;
    font-weight: 400;
    letter-spacing: -0.5px;
    line-height: 1;
    color: var(--ink);
  }
  .sender {
    position: absolute;
    right: 85px;
    top: 115px;
    text-align: right;
    font-size: 14.5px;
    line-height: 20px;
  }
  .sender__name { font-weight: 700; }
  .sender__role { font-weight: 300; }

  .rule {
    position: absolute;
    height: 1px;
    background: var(--ink);
  }
  .rule::before {
    content: "";
    position: absolute;
    left: 0;
    top: -1px;
    width: 74px;
    height: 3px;
    background: var(--green);
  }
  .rule--header { left: 85px; width: 678px; top: 174px; }
  .rule--footer { left: 83px; width: 530px; top: 1095px; }

  .contact {
    position: absolute;
    left: 626px;
    top: 1076px;
    display: flex;
    gap: 10px;
    align-items: flex-start;
  }
  .contact__icon { margin-top: 6px; }
  .contact__label { font-size: 12px; font-weight: 700; line-height: 18px; }
  .contact__phone { font-size: 12px; font-weight: 300; line-height: 20px; }
</style>
</head>
<body>
<main class="letterhead">
  <svg class="corner corner--top" width="848" height="60" viewBox="0 0 848 60" aria-hidden="true">
    <polygon points="396,0 520,0 640,30 600,36" fill="var(--grey)"/>
    <polygon points="470,0 660,0 768,34 716,43" fill="var(--ink)"/>
    <polygon points="660,0 848,0 848,60" fill="var(--green)"/>
  </svg>

  <header>
    <div class="brand-name">Northway Partners</div>
    <div class="sender">
      <div class="sender__name">Daniel Ashford</div>
      <div class="sender__role">Managing Director</div>
    </div>
    <div class="rule rule--header"></div>
  </header>

  <footer>
    <div class="rule rule--footer"></div>
    <div class="contact">
      <svg class="contact__icon" width="20" height="26" viewBox="0 0 20 26" aria-hidden="true">
        <path d="M3 1 h4 v8 h-3 c0 5 3 10 7 12 l2-2 5 3 -3 3 c-8 0 -14 -9 -14 -18 z" fill="var(--green)"/>
      </svg>
      <div>
        <div class="contact__label">CONTACT.</div>
        <div class="contact__phone">0400 555 019</div>
      </div>
    </div>
  </footer>

  <svg class="corner corner--bottom" width="848" height="60" viewBox="0 0 848 60" aria-hidden="true">
    <polygon points="216,33 249,30 414,60 300,60" fill="var(--grey)"/>
    <polygon points="87,30 138,24 336,60 150,60" fill="var(--ink)"/>
    <polygon points="0,6 168,60 0,60" fill="var(--green)"/>
  </svg>
</main>
</body>
</html>
```